WP website design for Kemble

We need a wordpress design that will incorporate a professional color scheme with company logo in a clean layout. The design needs to consider that this will be developed on a responsive theme. Colors are will be the green of the logo and any others that will creatively highlight it.

Industry/Entity Type

It Company

Font styles to use
Sans Serif

Requirements
Must have
• Navigation: 1) Home 2) Auctions 3) Auction Services 4) Sellers 5) TR Kemble Livestock 6) About Us 7) Contact Us
Site will have slideshow element, image attached.
Widgets will be: 1)Email Signup form 2) Featured Auctions widget 3) Social Media (FB, Youtube, RSS) 4) News & Events blog
Footer will have smaller company logo, association logos (attached) and contact info (below)
▪ T.R. Kemble Inc. / Auctioneers
▪ 4710 NC Hwy 91
▪ Cedarvale, NC 27000
▪ Office: (555) 318-6402
▪ Cell: (555) 274-8813
▪ email: trkemble@trkemble-example.com
Nice to have
• Site will have drop-down menus - please indicate the styling, for instance the dropdown menus

```html
<!DOCTYPE html>
<html lang="en">
<head>
<meta charset="utf-8">
<title>T.R. Kemble Inc. / Auctioneers</title>
<link rel="stylesheet" href="https://fonts.googleapis.com/css2?family=Open+Sans:ital,wght@0,400;0,600;0,700;1,400&family=Fenix&family=Cabin:wght@400;600&family=Arimo:ital,wght@0,400;0,700;1,400;1,700&display=swap">
<style>
:root{
  --green:#3a861c;
  --orange:#f6b23d;
  --bubble:#fbbd4f;
  --nav:#323232;
  --footer:#2a2a2a;
  --ink:#1e1e1e;
  --line:#d6d6d6;
  --white:#ffffff;
}
*{box-sizing:border-box;margin:0;padding:0}
html,body{width:929px;height:1200px;overflow:hidden}
body{position:relative;background:var(--white);font-family:"Arimo",Arial,sans-serif;color:var(--ink)}
.abs{position:absolute}

/* header */
.brand{left:86px;top:22px;width:150px;text-align:center;color:var(--green);font-family:"Fenix",serif}
.brand-mark{width:34px;height:34px;border-radius:50%;background:var(--green);margin:0 auto 6px}
.brand-name{font-size:20px;line-height:22px}
.brand-sub{font-size:14px;line-height:18px}
.social-title{left:715px;top:49px;font-family:"Open Sans",sans-serif;font-size:14px;font-weight:600;color:#222}
.social{left:710px;top:68px;display:flex;gap:5px}
.social span{width:30px;height:30px;border-radius:50%;display:flex;align-items:center;justify-content:center}
.s-a{background:#1e4f7a}.s-b{background:#2aa6dc}.s-rss{background:#f39a12}.s-mail{background:#c8c8c8}

/* navigation */
.nav{left:0;top:112px;width:929px;height:33px;background:var(--nav)}
.nav ul{list-style:none;display:flex;position:absolute;left:83px;top:0;height:33px}
.nav li{font-family:"Open Sans",sans-serif;font-size:9.5px;font-weight:600;color:var(--white);padding:0 11px;line-height:33px;text-transform:uppercase;white-space:nowrap}
.nav li.active{background:var(--green)}
.nav-arrow{left:246px;top:145px;width:0;height:0;border-left:6px solid transparent;border-right:6px solid transparent;border-top:6px solid var(--nav)}
.dropdown{left:198px;top:152px;width:144px;height:59px;background:#3b3b3b;border:1px solid #555;border-radius:2px;padding:5px 6px;z-index:3}
.dropdown div{font-family:"Fenix",serif;font-size:11px;color:var(--white);height:20px;line-height:20px;padding-left:8px;white-space:nowrap}
.dropdown .on{background:var(--green)}
.dropdown .sep{height:1px;background:#5a5a5a;margin:3px 0}

/* hero */
.hero-bg{left:0;top:145px;width:929px;height:273px;background:linear-gradient(#d2d2d2,#f4f4f4)}
.band{left:0;top:418px;width:929px;height:259px;background:var(--green)}
.slide{left:82px;top:150px;width:763px;height:296px;border:3px solid var(--white);box-shadow:0 1px 4px rgba(0,0,0,.35);
  background:linear-gradient(#f0f3f6 0%,#e9d8b0 28%,#d9a95a 40%,#6b7a4e 50%,#5c6b72 62%,#8a8f8a 80%,#c8a060 100%)}
.signup{left:586px;top:199px;width:245px;height:191px;background:rgba(55,55,55,.93);border:1px solid #777;padding:8px 16px}
.signup h3{font-family:"Cabin",sans-serif;font-weight:400;font-size:21px;color:var(--orange);letter-spacing:.5px;white-space:nowrap}
.signup p{font-family:"Open Sans",sans-serif;font-size:9px;color:var(--white);line-height:12px;margin-top:2px}
.field{width:198px;height:22px;background:var(--white);margin-top:12px;font-family:"Open Sans",sans-serif;font-size:9.5px;color:#888;padding:5px 6px}
.field+.field{margin-top:18px}
.subscribe{margin-top:18px;width:107px;height:28px;border-radius:14px;background:var(--white);border:2px solid #4aa9a4;font-family:"Open Sans",sans-serif;font-weight:600;font-size:10px;color:#222;text-align:center;line-height:24px}

/* welcome + testimonials */
.welcome-h{left:82px;top:476px;font-family:"Fenix",serif;font-size:26px;font-weight:400;color:var(--orange);white-space:nowrap}
.portrait{left:85px;top:523px;width:122px;height:117px;border:4px solid var(--white);background:linear-gradient(135deg,#c8ccd0,#8a9099 60%,#4b5360)}
.welcome-p{left:223px;top:524px;width:355px;font-size:10.4px;line-height:15.5px;color:var(--white)}
.welcome-p p+p{margin-top:15.5px}
.testi-h{left:598px;top:476px;font-family:"Fenix",serif;font-size:26px;font-weight:400;color:var(--white)}
.bubble{left:604px;top:515px;width:245px;height:129px;background:var(--bubble);border-radius:10px;padding:14px 16px 0 18px;font-style:italic;font-size:9.2px;line-height:17px;color:#222}
.bubble-tail{left:785px;top:643px}
.q{font-family:"Fenix",serif;font-style:normal;font-size:16px;font-weight:700;line-height:0}

/* listings */
.card{left:93px;width:491px;height:181px;border:1px solid var(--line);border-radius:4px;box-shadow:0 0 2px rgba(0,0,0,.08)}
.card h4{position:absolute;left:13px;top:16px;font-size:10.4px;font-weight:700;letter-spacing:.6px;color:#1c1c1c;white-space:nowrap}
.card .photo{position:absolute;left:12px;top:43px;width:170px;height:85px;background:linear-gradient(#5b8fd0 0%,#a7c5e6 40%,#c9b9a0 55%,#8b7a62 75%,#4f8b2d 88%,#3d7a23 100%)}
.btn{position:absolute;top:138px;height:26px;font-family:"Fenix",serif;font-size:13px;color:var(--white);display:flex;align-items:center;gap:6px;padding-left:8px}
.btn-details{left:12px;width:80px;background:#1c1c1c}
.btn-gallery{left:103px;width:80px;background:var(--green)}
.dot{width:13px;height:13px;border-radius:50%;background:var(--orange)}
.sq{width:14px;height:11px;border:2px solid var(--orange);border-radius:2px}
.card .info{position:absolute;left:194px;top:44px;width:285px;font-size:9px;font-style:italic;line-height:14px;color:#222}
.info .type{font-style:normal;font-weight:700;font-size:11px;color:var(--green);letter-spacing:.4px;margin-bottom:5px}
.info .lbl{color:#d9921f;font-weight:700}
.info p{margin-bottom:6px}
.info .extra{margin-top:9px}

/* sidebar */
.widget{left:617px;width:236px;border:1px solid var(--line);border-radius:4px}
.widget h5{font-weight:700;font-size:17px;color:var(--green);letter-spacing:.4px;white-space:nowrap}
.feat{top:702px;height:187px;padding:5px 14px}
.feat .link{font-family:"Open Sans",sans-serif;font-size:9.5px;color:var(--green);text-decoration:underline;letter-spacing:.3px;margin-top:2px;white-space:nowrap}
.feat .thumb{width:124px;height:60px;margin:6px 0 0 10px;border:2px solid #ddd;background:linear-gradient(#9fc3e6,#c8b9a0 50%,#5d8f3a 80%)}
.feat .date{font-size:9.5px;margin-top:8px;white-space:nowrap}
.feat .txt{font-size:9.5px;line-height:11px;margin-top:2px;width:175px}
.readmore{display:inline-block;margin-top:10px;background:#2a2a44;color:var(--white);font-size:9px;font-style:italic;font-weight:700;padding:2px 6px;border-radius:4px}
.news{top:905px;height:180px;padding:8px 12px 6px 16px}
.news-item{display:flex;gap:8px;margin-top:21px}
.news-item+.news-item{margin-top:8px}
.news-item .thumb{width:72px;height:52px;flex:none;background:linear-gradient(#5b8fd0,#b8c9dc 40%,#bfa88a 60%,#4f8b2d 90%)}
.news-item .d{font-size:9px;color:var(--green);margin-top:2px;white-space:nowrap}
.news-item .t{font-size:9.2px;line-height:14px;color:#333;margin-top:3px;white-space:nowrap}

/* footer */
.footer{left:0;top:1111px;width:929px;height:89px;background:var(--footer)}
.footer-info{left:81px;top:1117px;font-size:10.5px;line-height:15.6px;color:var(--white);font-style:normal;white-space:nowrap}
.badges{left:558px;top:1140px;display:flex;gap:12px;align-items:center}
.b1{width:56px;height:22px;background:#cfcfcf;border-radius:3px}
.b2{width:30px;height:28px;background:#cfcfcf;border-radius:4px}
.b3{width:38px;height:38px;border-radius:50%;background:#cfcfcf}
.footer-brand{left:742px;top:1124px;width:110px;text-align:center;font-family:"Fenix",serif;color:#d8d8d8}
.footer-brand .mk{width:26px;height:26px;border-radius:50%;background:#d8d8d8;margin:0 auto 4px}
.footer-brand .n{font-size:15px;line-height:17px}
.footer-brand .s{font-size:11px;line-height:14px}
</style>
</head>
<body>

<header>
  <div class="abs brand">
    <div class="brand-mark"></div>
    <div class="brand-name">T.R. Kemble</div>
    <div class="brand-sub">Inc. / Auctioneers</div>
  </div>
  <div class="abs social-title">Social Media</div>
  <div class="abs social">
    <span class="s-a" role="img" aria-label="Social network profile"></span>
    <span class="s-b" role="img" aria-label="Short news feed"></span>
    <span class="s-rss" role="img" aria-label="RSS feed">
      <svg width="14" height="14" viewBox="0 0 14 14"><circle cx="3" cy="11" r="1.8" fill="#fff"/><path d="M1.5 6a6.5 6.5 0 0 1 6.5 6.5" stroke="#fff" stroke-width="1.8" fill="none"/><path d="M1.5 2a10.5 10.5 0 0 1 10.5 10.5" stroke="#fff" stroke-width="1.8" fill="none"/></svg>
    </span>
    <span class="s-mail" role="img" aria-label="Email">
      <svg width="14" height="10" viewBox="0 0 14 10"><rect x="0.5" y="0.5" width="13" height="9" fill="#fff"/><path d="M0.5 0.5 7 6 13.5 0.5" stroke="#c8c8c8" fill="none"/></svg>
    </span>
  </div>
</header>

<nav class="abs nav">
  <ul>
    <li>Home</li>
    <li>Auctions</li>
    <li class="active">Auction Services</li>
    <li>Sellers</li>
    <li>TR Kemble Livestock</li>
    <li>About Us</li>
    <li>Contact Us</li>
  </ul>
</nav>

<div class="abs hero-bg"></div>
<div class="abs band"></div>
<div class="abs slide" role="img" aria-label="Slideshow photo of a calm lake reflecting autumn trees and golden grass"></div>
<div class="abs nav-arrow"></div>
<div class="abs dropdown">
  <div class="on">» Our Featured Listings</div>
  <div class="sep"></div>
  <div>» MLS Property</div>
</div>

<form class="abs signup">
  <h3>Email Sign Up Form</h3>
  <p>Lorem ipsum dolor sit amet, consectetuer adipiscing elit. Nam</p>
  <div class="field">Your Name</div>
  <div class="field">Email Address</div>
  <div class="subscribe">Subscribe Now</div>
</form>

<section>
  <h2 class="abs welcome-h">Welcome To Kemble Auctioneers</h2>
  <div class="abs portrait" role="img" aria-label="Portrait photo of the company auctioneer"></div>
  <div class="abs welcome-p">
    <p>Lorem ipsum dolor sit amet, consectetur adipisicing elit, sed do eiusmod tempor incididunt ut labore et dolore magna aliqua. Ut enim ad minim veniam, quis nostrud exercitation ullamco laboris nisi ut aliquipin voluptate velit esse cillum dolore eu fugiat nulla pariatur.</p>
    <p>Excepteur sint occaecat cupidatat non proident, sunt in culpa qui officia deserunt mollit anim id est laborum.is simply dummy text .</p>
  </div>
  <h2 class="abs testi-h">Testimonials</h2>
  <blockquote class="abs bubble"><span class="q">“</span> Lorem ipsum dolor sit amet, consectetur adip- isicing elit, sed do eiusmod tempor incididunt ut labore et dolore magna aliqua. Ut enim ad minim veniam, quis nostrud exercitation ullamco laboris teur sint occaecat cupidatat non proident, sunt in culpa qui officia deserunt mollit <span class="q">”</span></blockquote>
  <svg class="abs bubble-tail" width="22" height="18" viewBox="0 0 22 18"><path d="M0 0H18L22 18Z" fill="#fbbd4f"/></svg>
</section>

<article class="abs card" style="top:702px">
  <h4>2005 STONEKEY TEXT OF THE PRINTING AND EVERPINE 34-FT. CAMPER</h4>
  <div class="photo" role="img" aria-label="Photo of a two-storey brick house"></div>
  <div class="btn btn-details"><span class="dot"></span>Details</div>
  <div class="btn btn-gallery"><span class="sq"></span>Gallery</div>
  <div class="info">
    <div class="type">LIVE ON-SITE AUCTION</div>
    <p><span class="lbl">Begins:</span>&nbsp; Tuesday, April 23, 2013 at 10:00 AM EDT</p>
    <p><span class="lbl">Location:</span>&nbsp; Cedar Pond Entrance- 1450 W. Ridge Hwy 40&nbsp; text of the printing and typesetting industry. Lorem Ipsum has been the industry's standard dummy text ever since the 1500s,</p>
    <p class="extra">Cedar Pond Rd (Auction Property) Lake Ipsum has been the industry's standard dummy text ever Ridgefield, FL 34012</p>
  </div>
</article>

<article class="abs card" style="top:903px">
  <h4>2005 STONEKEY TEXT OF THE PRINTING AND EVERPINE 34-FT. CAMPER</h4>
  <div class="photo" role="img" aria-label="Photo of a two-storey brick house"></div>
  <div class="btn btn-details"><span class="dot"></span>Details</div>
  <div class="btn btn-gallery"><span class="sq"></span>Gallery</div>
  <div class="info">
    <div class="type">LIVE ON-SITE AUCTION</div>
    <p><span class="lbl">Begins:</span>&nbsp; Tuesday, April 23, 2013 at 10:00 AM EDT</p>
    <p><span class="lbl">Location:</span>&nbsp; Cedar Pond Entrance- 1450 W. Ridge Hwy 40&nbsp; text of the printing and typesetting industry. Lorem Ipsum has been the industry's standard dummy text ever since the 1500s,</p>
    <p class="extra">Cedar Pond Rd (Auction Property) Lake Ipsum has been the industry's standard dummy text ever Ridgefield, FL 34012</p>
  </div>
</article>

<aside class="abs widget feat">
  <h5>FEATURED AUCTIONS</h5>
  <div class="link">TRACTOR * HI LIFT * MACHINERY</div>
  <div class="thumb" role="img" aria-label="Photo of an estate house with palm trees"></div>
  <div class="date"><b>Saturday</b> March 16, 2013 at 10:00 AM</div>
  <div class="txt">simply dummy text of the printing and typesetting industry.</div>
  <span class="readmore">read more</span>
</aside>

<aside class="abs widget news">
  <h5>NEWS &amp; EVENTS</h5>
  <div class="news-item">
    <div class="thumb" role="img" aria-label="Photo of a house"></div>
    <div><div class="d">SATURDAY MARCH 6, 2014</div><div class="t">Lorem Ipsum is that it<br>has a more-or-less</div></div>
  </div>
  <div class="news-item">
    <div class="thumb" role="img" aria-label="Photo of a house"></div>
    <div><div class="d">SATURDAY MARCH 6, 2014</div><div class="t">Lorem Ipsum is that it<br>has a more-or-less</div></div>
  </div>
</aside>

<footer>
  <div class="abs footer"></div>
  <address class="abs footer-info">
    T.R. Kemble Inc. / Auctioneers<br>
    4710 NC Hwy 91 Cedarvale, NC 27000<br>
    Office: (555) 318-6402<br>
    Cell: (555) 274-8813<br>
    email: trkemble@trkemble-example.com
  </address>
  <div class="abs badges">
    <span class="b1" role="img" aria-label="Partner association badge"></span>
    <span class="b2" role="img" aria-label="Industry partner badge"></span>
    <span class="b3" role="img" aria-label="Livestock association badge"></span>
  </div>
  <div class="abs footer-brand">
    <div class="mk"></div>
    <div class="n">T.R. Kemble</div>
    <div class="s">Inc. / Auctioneers</div>
  </div>
</footer>

</body>
</html>
```